I would like a business card to match my truck wrap and logo. I would like the font to match my existing business card please.

Industry/Entity Type

Painter

Contact Information for Business Card

Rodrigo Fenwar 801-437-2190 Fenwarcoatings.utah@brelmox.com
SERVICES - Custom Paint & Stain, Interior & Exterior, Epoxy Coatings / Garage Floors, Cabinet Refinishing, Log Staining and Refinishing.

Requirements
Nice to have
• I would like to have the white and grey line like the bottom of my vehicle wrap, Light Grey to match my truck also.

```html
<!DOCTYPE html>
<html lang="en">
<head>
<meta charset="utf-8">
<title>Fenwar Coatings – Business Card</title>
<link rel="stylesheet" href="https://fonts.googleapis.com/css2?family=Archivo:wght@900&family=Arimo:wght@400;700&display=swap">
<style>
  :root {
    --bg: #e3e4e6;
    --card-white: #f4f4f4;
    --card-grey: #8b909b;
    --band: #aeb5c3;
    --brand-blue: #1b86d1;
    --ink: #2c2c2c;
    --white: #ffffff;
  }
  * { margin: 0; padding: 0; box-sizing: border-box; }
  html, body { width: 1200px; height: 930px; overflow: hidden; background: var(--bg); }
  .canvas { position: relative; width: 1200px; height: 930px; }
  .card {
    position: absolute; left: 300px; width: 600px; height: 343px;
    overflow: hidden; box-shadow: 0 8px 22px rgba(0,0,0,.12);
  }
  .card--front { top: 100px; background: var(--card-white); }
  .card--back  { top: 487px; background: var(--card-grey); }

  /* Front */
  .front-band { position: absolute; left: 0; bottom: 0; width: 600px; height: 80px; }
  .holder-name {
    position: absolute; left: 56px; top: 118px;
    font-family: "Archivo", sans-serif; font-weight: 900; font-size: 23px;
    letter-spacing: .5px; color: var(--brand-blue); text-transform: uppercase;
  }
  .contact-list { position: absolute; left: 56px; top: 158px; list-style: none;
    font-family: "Arimo", sans-serif; font-size: 15px; color: var(--ink); }
  .contact-list li { display: flex; align-items: center; gap: 8px; margin-bottom: 6px; }
  .contact-list svg { width: 14px; height: 14px; fill: var(--brand-blue); flex: none; }

  .company { position: absolute; display: flex; align-items: center; gap: 12px; }
  .company--front { left: 348px; top: 136px; }
  .company-mark { width: 30px; height: 30px; background: var(--brand-blue); flex: none; }
  .company-name {
    font-family: "Arimo", sans-serif; font-weight: 700; font-size: 24px;
    line-height: 1; color: var(--brand-blue); white-space: nowrap;
  }

  /* Back */
  .back-content { position: absolute; inset: 0; display: flex; flex-direction: column;
    align-items: center; justify-content: center; text-align: center; color: var(--white); }
  .company--back { position: static; margin-bottom: 26px; }
  .company--back .company-name { color: var(--white); font-size: 34px; }
  .services-title { font-family: "Arimo", sans-serif; font-weight: 700; font-size: 17px;
    letter-spacing: 1px; margin-bottom: 6px; }
  .services-list { list-style: none; font-family: "Arimo", sans-serif; font-size: 14px;
    line-height: 1.35; letter-spacing: .5px; text-transform: uppercase; }
</style>
</head>
<body>
<main class="canvas">

  <section class="card card--front" aria-label="Business card front">
    <svg class="front-band" viewBox="0 0 600 80" aria-hidden="true">
      <path d="M0 22 L330 22 L360 10 L600 10 L600 80 L0 80 Z" fill="var(--band)"/>
      <path d="M0 14 L328 14 L358 2 L600 2" fill="none" stroke="var(--band)" stroke-width="3"/>
    </svg>

    <h1 class="holder-name">Rodrigo Fenwar</h1>
    <ul class="contact-list">
      <li>
        <svg viewBox="0 0 24 24" aria-hidden="true"><path d="M6.6 10.8a15.1 15.1 0 0 0 6.6 6.6l2.2-2.2c.3-.3.7-.4 1-.2 1.1.4 2.3.6 3.6.6.6 0 1 .4 1 1V20c0 .6-.4 1-1 1A17 17 0 0 1 3 4c0-.6.4-1 1-1h3.5c.6 0 1 .4 1 1 0 1.3.2 2.5.6 3.6.1.3 0 .7-.2 1L6.6 10.8z"/></svg>
        <span>801-437-2190</span>
      </li>
      <li>
        <svg viewBox="0 0 24 24" aria-hidden="true"><path d="M2 5h20v14H2z M2 5l10 8 10-8" fill="var(--brand-blue)" stroke="var(--card-white)" stroke-width="1.5"/></svg>
        <span>Fenwarcoatings.utah@brelmox.com</span>
      </li>
    </ul>

    <div class="company company--front">
      <span class="company-mark" aria-hidden="true"></span>
      <p class="company-name">Fenwar Coatings</p>
    </div>
  </section>

  <section class="card card--back" aria-label="Business card back">
    <div class="back-content">
      <div class="company company--back">
        <p class="company-name">Fenwar Coatings</p>
      </div>
      <h2 class="services-title">SERVICES</h2>
      <ul class="services-list">
        <li>Custom Paint &amp; Stain</li>
        <li>Interior &amp; Exterior</li>
        <li>Epoxy Coatings / Garage Floors</li>
        <li>Cabinet Refinishing</li>
        <li>Log Staining and Refinishing.</li>
      </ul>
    </div>
  </section>

</main>
</body>
</html>
```